New Design for Willow Glow & Laser

The name of our company is Willow Glow & Laser, and this is our current website: www.WillowGlowLaser.example. We are looking for a fresh design mock-up of our website.
What is important to us?
> We want to maintain the same navigation.
> We want to use the same content (e.g., text, pictures, etc.)
> We want to maintain the color scheme.
> The website aims to get visitors to BOOK ONLINE or BUY ONLINE.
Essential instructions for designers:
> Please visit our current website and our social media accounts to get a better idea of our brand design.
> We want a mockup design for our home page, service page, pricing page, before & after page, shop deals page, careers page, contact pages, and blog pages.
> Color codes: #faa641, #222222, #fffffe, #ea8103
Target Market(s)
women 25 - 45
Number of Pages Required
5+ page

```html
<!DOCTYPE html>
<html lang="en">
<head>
<meta charset="utf-8">
<title>Willow Glow &amp; Laser</title>
<link href="https://fonts.googleapis.com/css2?family=Poppins:wght@400;600;700;800&family=Lato:wght@400;700&display=swap" rel="stylesheet">
<style>
:root{
  --orange:#faa641;
  --orange-deep:#ea8103;
  --ink:#222222;
  --black:#000000;
  --white:#fffffe;
  --muted:#555555;
  --heading:'Poppins',sans-serif;
  --body:'Lato',sans-serif;
}
*{box-sizing:border-box;margin:0;padding:0}
html,body{width:1200px;height:3058px;overflow:hidden;background:var(--white);font-family:var(--body);color:var(--ink)}
.wrap{width:974px;margin:0 auto;position:relative}

/* header */
.site-header{height:102px;display:flex;align-items:center}
.site-header .wrap{display:flex;align-items:center;justify-content:space-between}
.brand{display:flex;align-items:center;gap:10px;font-family:var(--heading);font-weight:800;color:var(--ink);line-height:1;white-space:nowrap}
.brand-name{font-size:26px;letter-spacing:.5px}
.brand-dot{width:40px;height:40px;border-radius:50%;background:var(--orange);flex:none}
.main-nav{display:flex;gap:28px;font-size:15px;white-space:nowrap}
.btn{display:inline-flex;align-items:center;justify-content:center;border-radius:20px;font-family:var(--body);font-weight:700;font-size:16px;height:38px;white-space:nowrap}
.btn-orange{background:var(--orange);color:var(--white)}
.btn-outline{border:2px solid var(--white);color:var(--white)}
.btn-white{background:var(--white);color:var(--orange)}

/* hero */
.hero{position:relative;height:664px}
.hero-photo{position:absolute;inset:0;background:linear-gradient(120deg,#6d5a4c,#3f3835 45%,#2b2726)}
.hero-curve{position:absolute;left:0;bottom:0;width:1200px;height:140px}
.hero-content{position:relative;text-align:center;color:var(--white);padding-top:150px}
.hero h1{font-family:var(--heading);font-weight:800;font-size:80px;line-height:1;letter-spacing:-1px}
.hero p{font-family:var(--heading);font-size:27px;line-height:41px;width:820px;margin:20px auto 0}
.hero-actions{display:flex;gap:20px;justify-content:center;margin-top:10px}
.hero-actions .btn{width:172px}
.play{width:66px;height:66px;border-radius:50%;background:var(--orange);margin:32px auto 0;display:flex;align-items:center;justify-content:center;box-shadow:0 0 0 4px rgba(255,255,255,.35)}

/* offers */
.offers{padding-top:58px;text-align:center}
.section-title{font-family:var(--heading);font-weight:700;font-size:40px;color:var(--black)}
.offer-list{display:flex;justify-content:space-between;margin-top:62px}
.offer{width:190px;text-align:center}
.offer-photo{width:170px;height:170px;border-radius:50%;margin:0 auto;background:linear-gradient(135deg,#d9b9a4,#6b5a55)}
.offer h3{font-family:var(--heading);font-weight:700;font-size:22px;line-height:30px;color:var(--orange);margin-top:14px;white-space:nowrap}

/* about */
.about{margin-top:80px;background:var(--orange);height:466px;position:relative}
.about-photo{position:absolute;left:14px;top:15px;width:497px;height:434px;background:linear-gradient(135deg,#8a9a8c,#3d4a56)}
.about-text{position:absolute;left:583px;top:62px;width:500px;color:var(--white)}
.about-text h2{font-family:var(--heading);font-weight:700;font-size:36px;line-height:1.2;white-space:nowrap}
.about-text p{font-size:15px;line-height:22.5px;margin-top:22px}
.about-text p + p{margin-top:14px}
.about-text .btn{width:172px;margin-top:32px}

/* testimonials */
.reviews{padding-top:70px;text-align:center}
.review-list{display:flex;justify-content:space-between;margin-top:36px;text-align:left}
.review{width:305px}
.review-card{height:197px;border:1px solid #888;padding:16px 18px;position:relative;background:var(--white)}
.review-card::after{content:"";position:absolute;left:52px;bottom:-12px;width:20px;height:20px;background:var(--white);border-right:1px solid #888;border-bottom:1px solid #888;transform:rotate(45deg)}
.quote{font-family:var(--heading);font-weight:800;color:var(--orange);font-size:34px;line-height:28px;height:22px}
.stars{font-size:11px;letter-spacing:1px;color:var(--black);margin-top:4px}
.review-card p{font-size:15px;line-height:22.5px;color:var(--muted);margin-top:10px}
.reviewer{display:flex;align-items:center;gap:10px;margin:16px 0 0 84px;font-family:var(--heading);font-weight:600;color:var(--orange);font-size:15px}
.avatar{width:48px;height:48px;border-radius:50%;background:var(--orange);color:var(--white);display:flex;align-items:center;justify-content:center;font-size:20px}
.dots{display:flex;gap:14px;justify-content:center;margin-top:34px}
.dots span{width:10px;height:10px;border-radius:50%;background:var(--black)}
.dots span.active{width:13px;height:13px;margin-top:-1px;background:var(--orange)}

/* gallery */
.gallery{margin-top:84px;height:134px;display:flex;position:relative}
.gallery-item{flex:1;height:100%}
.g1{background:linear-gradient(135deg,#2a2322,#4b3a36)}
.g2{background:linear-gradient(135deg,#c8a98f,#5b4a44)}
.g3{background:linear-gradient(135deg,#a8aeb2,#4b5055)}
.g4{background:linear-gradient(135deg,#8b7c74,#2f2a29)}
.g5{background:linear-gradient(135deg,#b7a89a,#494140)}
.g6{background:linear-gradient(135deg,#3a302e,#6b5550)}
.arrow{position:absolute;top:49px;width:36px;height:36px;border-radius:50%;background:var(--white);display:flex;align-items:center;justify-content:center}

/* newsletter */
.newsletter{background:var(--orange);height:186px}
.newsletter .wrap{display:flex;align-items:center;justify-content:space-between;height:100%}
.newsletter h2{font-family:var(--heading);font-weight:700;color:var(--white);font-size:30px;display:flex;align-items:center;gap:16px}
.subscribe{width:452px;height:60px;background:var(--white);border-radius:3px;display:flex;align-items:center;justify-content:space-between;padding:0 8px 0 18px;font-size:10px;color:var(--ink)}
.subscribe .btn{width:124px;height:38px;font-size:15px}

/* footer */
.site-footer{background:var(--black);height:423px;color:var(--white);position:relative}
.footer-cols{display:flex;padding-top:74px}
.footer-brand{width:425px;padding-top:26px}
.footer-brand .brand{color:var(--white)}
.footer-brand .brand-name{font-size:32px}
.footer-brand .brand-dot{width:54px;height:54px}
.footer-brand h3{font-family:var(--body);font-weight:700;font-size:21px;line-height:26px;margin-top:32px}
.footer-brand .btn{width:150px;margin-top:26px}
.footer-col h4{font-family:var(--body);font-weight:700;font-size:21px;white-space:nowrap}
.quick{width:198px}
.quick ul{list-style:none;margin-top:20px;font-size:14px;line-height:30px}
.touch{width:230px}
.touch li{list-style:none;display:flex;align-items:center;gap:12px;font-size:17px;margin-top:20px}
.touch ul{margin-top:12px}
.follow li{list-style:none;display:flex;align-items:center;gap:14px;font-size:14px;margin-top:8px;white-space:nowrap}
.follow ul{margin-top:16px}
.social-dot{width:22px;height:22px;border-radius:50%;background:var(--white);flex:none}
.copyright{position:absolute;left:150px;right:150px;bottom:0;border-top:1px solid #333;text-align:center;font-size:13px;height:48px;line-height:40px}
</style>
</head>
<body>

<header class="site-header">
  <div class="wrap">
    <div class="brand"><span class="brand-dot"></span><span class="brand-name">WILLOW GLOW &amp; LASER</span></div>
    <nav class="main-nav"><span>Home</span><span>Services</span><span>Pricing</span><span>About</span><span>Blog</span><span>Contact</span></nav>
    <span class="btn btn-orange" style="width:172px">Book Online</span>
  </div>
</header>

<section class="hero">
  <div class="hero-photo" role="img" aria-label="Technician performing a facial treatment on a client in the clinic"></div>
  <svg class="hero-curve" viewBox="0 0 1200 140" preserveAspectRatio="none"><path d="M0,0 Q600,230 1200,0 L1200,140 L0,140 Z" fill="var(--white)"/></svg>
  <div class="hero-content">
    <h1>Your Skin Deserves It</h1>
    <p>Laser Center &amp; Medispa Located In Downtown Marlow, Brisa,<br>Calden, &amp; Vesta.</p>
    <div class="hero-actions"><span class="btn btn-orange">Book Online</span><span class="btn btn-outline">Shop Deals</span></div>
    <div class="play"><svg width="26" height="30" viewBox="0 0 26 30"><path d="M2 1 L25 15 L2 29 Z" fill="var(--white)"/></svg></div>
  </div>
</section>

<section class="offers">
  <div class="wrap">
    <h2 class="section-title">What We Offer</h2>
    <div class="offer-list">
      <div class="offer"><div class="offer-photo" role="img" aria-label="Photofacial treatment"></div><h3>Photofacials</h3></div>
      <div class="offer"><div class="offer-photo" role="img" aria-label="Wrinkle relaxer injection close-up"></div><h3>Wrinkle Relaxer<br>Injections</h3></div>
      <div class="offer"><div class="offer-photo" role="img" aria-label="Laser hair removal session"></div><h3>Laser<br>Hair Removal</h3></div>
      <div class="offer"><div class="offer-photo" role="img" aria-label="Facial and peel treatment"></div><h3>Facials &amp; Peels</h3></div>
      <div class="offer"><div class="offer-photo" role="img" aria-label="Lip shaping treatment"></div><h3>Lip Shape<br>&amp; Enhancement</h3></div>
    </div>
  </div>
</section>

<section class="about">
  <div class="about-photo" role="img" aria-label="Two smiling team members holding membership brochures"></div>
  <div class="about-text">
    <h2>About Willow Glow &amp; Laser</h2>
    <p>At Willow Glow &amp; Laser, we've always believed that caring about your skin and your appearance is not selfish, it is self-care. It's time to be proud of the steps you take to look your best and it's time you ask for the best. Your skin deserves it.</p>
    <p>Willow Glow brings to you the latest technology, techniques, and the best professionals to deliver the results you want guaranteed.It's time to cross out the judgment, the labels, the hesitation, and the regrets.We offer clinic locations in Calden, AZ, Marlow, AZ, Brisa, AZ and Vesta, AZ.</p>
    <span class="btn btn-white">Book Online</span>
  </div>
</section>

<section class="reviews">
  <div class="wrap">
    <h2 class="section-title">What Our Happy Clients Say</h2>
    <div class="review-list">
      <div class="review">
        <div class="review-card"><div class="quote">“</div><div class="stars">★★★★★</div><p>"I have been going to Willow Glow &amp; Laser for 2 years now. I am very pleased with my laser hair reduction results."</p></div>
        <div class="reviewer"><span class="avatar">M</span>–&nbsp;Maren D</div>
      </div>
      <div class="review">
        <div class="review-card"><div class="quote">“</div><div class="stars">★★★★★</div><p>Lena is my technician and I love her! Always goes the extra mile to make sure areas are covered, and that I'm getting the best result. I couldn't be happier."</p></div>
        <div class="reviewer"><span class="avatar">T</span>–&nbsp;Tessa C</div>
      </div>
      <div class="review">
        <div class="review-card"><div class="quote">“</div><div class="stars">★★★★★</div><p>I have been going to Willow Glow, for over a year and am very satisfied with the services and the staff."</p></div>
        <div class="reviewer"><span class="avatar">R</span>–&nbsp;Rosa M</div>
      </div>
    </div>
    <div class="dots"><span></span><span class="active"></span><span></span></div>
  </div>
</section>

<section class="gallery">
  <div class="gallery-item g1" role="img" aria-label="Client portrait"></div>
  <div class="gallery-item g2" role="img" aria-label="Technician treating a client"></div>
  <div class="gallery-item g3" role="img" aria-label="Team members with brochures"></div>
  <div class="gallery-item g4" role="img" aria-label="Facial treatment in progress"></div>
  <div class="gallery-item g5" role="img" aria-label="Consultation with tablet"></div>
  <div class="gallery-item g6" role="img" aria-label="Client portrait in profile"></div>
  <span class="arrow" style="left:53px"><svg width="14" height="14" viewBox="0 0 14 14"><path d="M9 2 L4 7 L9 12" stroke="var(--black)" stroke-width="2.4" fill="none"/></svg></span>
  <span class="arrow" style="right:53px"><svg width="14" height="14" viewBox="0 0 14 14"><path d="M5 2 L10 7 L5 12" stroke="var(--black)" stroke-width="2.4" fill="none"/></svg></span>
</section>

<section class="newsletter">
  <div class="wrap">
    <h2><svg width="40" height="40" viewBox="0 0 40 40" fill="none" stroke="var(--white)" stroke-width="2"><path d="M2 16 L20 4 L38 16 V38 H2 Z"/><path d="M2 16 L20 28 L38 16"/><path d="M10 12 H30 M10 17 H30"/></svg>Subscribe To Our Newsletter</h2>
    <div class="subscribe"><span>Your Email Address...</span><span class="btn btn-orange">Submit</span></div>
  </div>
</section>

<footer class="site-footer">
  <div class="wrap footer-cols">
    <div class="footer-brand">
      <div class="brand"><span class="brand-dot"></span><span class="brand-name">WILLOW GLOW<br>&amp; LASER</span></div>
      <h3>If You Have Any Qusetions,Please<br>Contact Us.</h3>
      <span class="btn btn-orange">Get In Touch</span>
    </div>
    <div class="footer-col quick">
      <h4>Quick Links</h4>
      <ul><li>Home</li><li>Services</li><li>Pricing</li><li>About</li><li>Blog</li><li>Contact</li></ul>
    </div>
    <div class="footer-col touch">
      <h4>Get in Touch</h4>
      <ul>
        <li><svg width="14" height="18" viewBox="0 0 14 18"><path d="M7 1 C3.5 1 1 3.5 1 7 C1 11 7 17 7 17 C7 17 13 11 13 7 C13 3.5 10.5 1 7 1 Z" fill="var(--white)"/><circle cx="7" cy="7" r="2.3" fill="var(--black)"/></svg>Our Locations</li>
        <li><svg width="16" height="12" viewBox="0 0 16 12"><rect x="0.5" y="0.5" width="15" height="11" fill="var(--white)"/><path d="M0.5 0.5 L8 7 L15.5 0.5" stroke="var(--black)" fill="none"/></svg>Send an email</li>
      </ul>
    </div>
    <div class="footer-col follow">
      <h4>Follow Us</h4>
      <ul><li><span class="social-dot"></span>Community Page</li><li><span class="social-dot"></span>Photo Feed</li></ul>
    </div>
  </div>
  <div class="copyright">© 2024 Willow Glow &amp; Laser. All Rights Reserved.</div>
</footer>

</body>
</html>
```